'Little Lantern' promotional brochure

We have designed a 6 week program to educate impending first-time parents about the things they need to know to survive the first 6 months. Sessions delivered by general practitioner/family doctor, dietician, physiotherapist, speech pathologist and psychologist. Our promotional blurb is: 'A comprehensive education program for first-time parents-to-be, delivered over 6 weeks by health professionals in your community, about everything you need to know to look after your baby (and yourself!) in the first 6 months'. I now want to put together a promotional brochure to be distributed to those couples who express an interest which will provide further details of what will be delivered in the course.
Updates
In terms of layout, I envisaged a double sided A4 size, foldable into 3 sections, but very happy to be guided on this.
Target Market(s)
To appeal to a young, well educated demographic. First time parents couples.
Industry/Entity Type
Medical
Font styles to use
Other font styles liked:
- Playfair Display
Requirements
Must have
- Playfair display font to be consistent with our logo (attached). Logo also included please. Some consistency with colours of logo please.
Nice to have
- I am a doctor, and have no creative genes! But prefer a clean and professional appearance overall. Not too cluttered in overall appearance.
Should not have
- No cheesy pictures of babies.

```html
<!DOCTYPE html>
<html lang="en">
<head>
<meta charset="utf-8">
<title>Little Lantern – Brochure</title>
<link rel="stylesheet" href="https://fonts.googleapis.com/css2?family=Playfair+Display:wght@700&family=Arimo:wght@400;700&family=Archivo+Black&display=swap">
<style>
:root{
  --green:#6cc04a;
  --green-dark:#4f9f34;
  --green-pale:#e4f1dc;
  --grey-dark:#6d6e70;
  --grey-mid:#a7a9ab;
  --grey-light:#dcdddf;
  --paper:#f2f3f3;
  --ink:#231f20;
  --white:#ffffff;
}
*{margin:0;padding:0;box-sizing:border-box}
html,body{width:1200px;height:848px;overflow:hidden;background:var(--white)}
body{font-family:"Arimo",Arial,sans-serif;color:var(--ink)}
.brochure{position:relative;width:1200px;height:848px;overflow:hidden}
.panel{position:absolute;top:0;height:848px;width:400px;overflow:hidden}
.panel--sessions{left:0;background:var(--paper)}
.panel--team{left:400px;background:var(--green)}
.panel--cover{left:800px;background:var(--white)}
.panel-bg{position:absolute;inset:0;width:100%;height:100%}

/* Sessions */
.week-title{position:absolute;left:56px;font-family:"Playfair Display",Georgia,serif;font-weight:700;font-size:25px;color:var(--white)}
.session{position:absolute;left:26px;width:340px;font-size:16px;line-height:1.3;color:var(--ink)}
.session p+p{margin-top:18px}
.session strong{font-family:"Playfair Display",Georgia,serif;font-weight:700}
.photo-father{position:absolute;left:50px;top:578px;width:320px;height:270px;background:linear-gradient(160deg,#f4f4f4,#d9d9d9 60%,#c8c3be)}

/* Team */
.team-mark{position:absolute;left:175px;top:16px;width:50px;height:50px;border-radius:50%;background:var(--white);opacity:.85}
.team-title{position:absolute;top:66px;width:400px;text-align:center;font-family:"Playfair Display",Georgia,serif;font-weight:700;font-size:24px;color:var(--white)}
.member{position:absolute;left:58px;width:284px;height:36px;text-align:center;padding-top:3px;clip-path:polygon(4% 0,96% 0,100% 50%,96% 100%,4% 100%,0 50%)}
.member--dark{background:var(--grey-dark);color:var(--white)}
.member--light{background:var(--green-pale);color:var(--grey-dark)}
.member-name{font-family:"Playfair Display",Georgia,serif;font-weight:700;font-size:14px;line-height:17px}
.member-role{font-size:8.5px;line-height:11px;text-transform:uppercase;letter-spacing:.1px}
.portrait{position:absolute;width:60px;height:60px;transform:rotate(45deg);border:3px solid var(--white);background:linear-gradient(135deg,#e9d6c7,#a88f7e)}
.hours,.contact{position:absolute;left:26px;color:var(--white);font-size:14px;line-height:18px}
.info-title{font-family:"Playfair Display",Georgia,serif;font-weight:700;font-size:16px;color:var(--ink);text-transform:uppercase;margin-bottom:1px}
.contact .gap{margin-top:8px}

/* Cover */
.brand{position:absolute;left:30px;top:38px;display:flex;align-items:center;gap:14px}
.brand-mark{width:50px;height:50px;background:var(--green)}
.brand-name{font-family:"Playfair Display",Georgia,serif;font-weight:700;font-size:19px;line-height:19px;color:var(--grey-dark);text-transform:uppercase}
.photo-family{position:absolute;left:92px;top:296px;width:222px;height:222px;transform:rotate(45deg);border:6px solid var(--white);background:linear-gradient(135deg,#bfe0f0,#c7a58e 55%,#6f8b55);box-shadow:0 2px 10px rgba(0,0,0,.25)}
.title-band{position:absolute;left:0;top:648px;width:400px;height:48px;background:var(--white);display:flex;align-items:center;justify-content:center}
.cover-title{font-family:"Archivo Black",Arial,sans-serif;font-size:33px;color:var(--green);text-transform:uppercase;letter-spacing:.5px}
</style>
</head>
<body>
<main class="brochure">

  <section class="panel panel--sessions">
    <svg class="panel-bg" viewBox="0 0 400 848" aria-hidden="true">
      <polygon points="0,0 200,0 96,104" fill="var(--green)"/>
      <polygon points="200,0 330,0 220,110" fill="#e8efe4"/>
      <polygon points="214,0 270,0 242,28" fill="var(--grey-light)"/>
      <polygon points="0,0 0,150 110,40" fill="var(--green-dark)" opacity=".35"/>
      <polygon points="0,240 400,240 400,560 0,560" fill="#e7e8e9"/>
      <polygon points="0,264 196,264 96,364" fill="var(--green)"/>
      <polygon points="40,264 196,264 118,342" fill="var(--grey-dark)" opacity=".55"/>
      <polygon points="196,264 400,264 400,470" fill="#eceded"/>
      <polygon points="0,560 400,560 400,848 0,848" fill="#eef0ee"/>
    </svg>
    <h2 class="week-title" style="top:22px">Week 5</h2>
    <div class="session" style="top:114px">
      <p><strong>Session 1</strong> – Clinical Psychologist Dr Maren Lowell will share information about bonding &amp; attachment with your baby, how to promote their social &amp; emotional development and how to manage separation anxiety. She will also discuss positive parenting approaches.</p>
    </div>
    <h2 class="week-title" style="top:284px">Week 6</h2>
    <div class="session" style="top:374px">
      <p><strong>Session 1</strong> – Secret Men’s Business – a men-only session (including beer!) with a new father for frank discussion about the road ahead. Mums will do a shopping excursion with the GP &amp; Dietician to FreshWay to look at baby products and food – the good and the bad!</p>
      <p><strong>Session 2</strong> - Program review, reflection and evaluation and future session planning when baby is 6 months of age.</p>
    </div>
    <div class="photo-father" role="img" aria-label="Photo of a young father cradling his newborn baby"></div>
  </section>

  <section class="panel panel--team">
    <svg class="panel-bg" viewBox="0 0 400 848" aria-hidden="true">
      <polygon points="0,0 100,0 0,100" fill="var(--grey-light)"/>
      <polygon points="100,0 300,0 200,100" fill="#e9eae8"/>
      <polygon points="300,0 400,0 400,100" fill="var(--grey-light)"/>
      <polygon points="190,0 250,0 220,30" fill="var(--grey-dark)"/>
      <polygon points="400,460 400,848 200,848" fill="var(--green-dark)" opacity=".45"/>
      <polygon points="280,560 400,440 400,680" fill="#5fb03f"/>
    </svg>
    <div class="team-mark" aria-hidden="true"></div>
    <h2 class="team-title">The Team</h2>

    <div class="member member--dark" style="top:108px"><div class="member-name">Dr Helena Marsh</div><div class="member-role">MBBS FRACGP B SC GRAD DIP ED</div></div>
    <div class="member member--light" style="top:146px"><div class="member-name">Dr Julian Carter</div><div class="member-role">MBBS, FRACGP, B INT BUS, GDIP ECON</div></div>
    <div class="member member--dark" style="top:192px"><div class="member-name">Dr Nora Fitzgerald</div><div class="member-role">MB BCH BAO NUI, FRACGP, MICGP, DRCOG</div></div>
    <div class="member member--light" style="top:230px"><div class="member-name">Dr Sophie Granger</div><div class="member-role">MBBS</div></div>
    <div class="member member--dark" style="top:276px"><div class="member-name">Tessa Hollis</div><div class="member-role">Bachelor of Podiatry and Nursing</div></div>
    <div class="member member--light" style="top:314px"><div class="member-name">Dr Clara Weston</div><div class="member-role">MBBS</div></div>
    <div class="member member--dark" style="top:360px"><div class="member-name">Owen Mitchell</div><div class="member-role">B. Physiotherapy, B. Exercise Science</div></div>
    <div class="member member--light" style="top:398px"><div class="member-name">Leah Donovan</div><div class="member-role">BA of ExSci, Doctorate of Physiotherapy</div></div>
    <div class="member member--dark" style="top:444px"><div class="member-name">Amy Rowland</div><div class="member-role">Nutritionist</div></div>
    <div class="member member--light" style="top:482px"><div class="member-name">Kate Ellery</div><div class="member-role">Paediatric Speech Pathologist</div></div>
    <div class="member member--dark" style="top:528px"><div class="member-name">Mia Sutton</div><div class="member-role">B. HM &amp; ExSci / Grad Dip. Clinical Ex Phys</div></div>

    <div class="portrait" style="left:42px;top:114px" role="img" aria-label="Portrait of Dr Helena Marsh"></div>
    <div class="portrait" style="left:298px;top:114px" role="img" aria-label="Portrait of Dr Julian Carter"></div>
    <div class="portrait" style="left:42px;top:198px" role="img" aria-label="Portrait of Dr Nora Fitzgerald"></div>
    <div class="portrait" style="left:298px;top:198px" role="img" aria-label="Portrait of Dr Sophie Granger"></div>
    <div class="portrait" style="left:42px;top:282px" role="img" aria-label="Portrait of Tessa Hollis"></div>
    <div class="portrait" style="left:298px;top:282px" role="img" aria-label="Portrait of Dr Clara Weston"></div>
    <div class="portrait" style="left:42px;top:366px" role="img" aria-label="Portrait of Owen Mitchell"></div>
    <div class="portrait" style="left:298px;top:366px" role="img" aria-label="Portrait of Leah Donovan"></div>
    <div class="portrait" style="left:42px;top:450px" role="img" aria-label="Portrait of Amy Rowland"></div>
    <div class="portrait" style="left:298px;top:450px" role="img" aria-label="Portrait of Kate Ellery"></div>
    <div class="portrait" style="left:42px;top:532px" role="img" aria-label="Portrait of Mia Sutton"></div>

    <div class="hours" style="top:654px">
      <h3 class="info-title">Opening Hours</h3>
      <p>Monday to Friday: 8:30am – 5:00pm</p>
      <p>Saturday: 8:00am – 12:00pm</p>
      <p>Sunday &amp; Public Holidays:&nbsp; Closed</p>
    </div>
    <div class="contact" style="top:734px">
      <h3 class="info-title">Contact Information</h3>
      <p>Wattlebay Village Centre, Shop 7</p>
      <p>215 Harbour Lane, Wattlebay NSW 2490</p>
      <p class="gap">Phone: 02 5550 1234 &nbsp;• Fax: 02 5550 1299</p>
      <p>Email: hello@wattlebayhealth.example</p>
    </div>
  </section>

  <section class="panel panel--cover">
    <svg class="panel-bg" viewBox="0 0 400 848" aria-hidden="true">
      <polygon points="200,0 400,0 400,200" fill="#eef4ea"/>
      <polygon points="120,190 250,160 400,300 400,380" fill="var(--grey-dark)"/>
      <polygon points="250,160 400,160 400,300" fill="var(--green)"/>
      <polygon points="0,300 100,200 180,280 0,460" fill="#eceeeb"/>
      <polygon points="320,230 400,160 400,320" fill="var(--grey-mid)"/>
      <polygon points="0,560 120,560 0,680" fill="var(--green-pale)"/>
      <polygon points="40,700 400,700 400,848 180,848" fill="var(--green)"/>
      <polygon points="0,700 120,700 0,820" fill="var(--grey-light)"/>
      <polygon points="230,700 400,700 400,848" fill="var(--grey-mid)"/>
      <polygon points="80,848 180,740 280,848" fill="#eef1ec"/>
    </svg>
    <div class="brand">
      <span class="brand-mark" aria-hidden="true"></span>
      <span class="brand-name">Wattlebay<br>Health &amp;<br>Medical</span>
    </div>
    <div class="photo-family" role="img" aria-label="Photo of smiling parents holding their baby"></div>
    <div class="title-band"><h1 class="cover-title">Little Lantern</h1></div>
  </section>

</main>
</body>
</html>
```